Events Company Needs Website Revamp

Tallwood Expos is an events company that specializes in organizing and marketing large scale consumer and trade events globally.

The new web design should provide easy classification of the events, and allow visitors to find and access the details page within 2 clicks.

There are no strict guidelines on the color theme. It just has to blend naturally with the corporate logo.
Updates

The company logo is uploaded (pdf & ai)

I came across this design which I like very much. Elegant and corporate with nice modern fonttype.

Layout wise, neat and clear. 

Please see how you can emulate the design further. Particularly, highlighting the 2 event arms (Trade/Consumer) clearly.

Target Market(s)

Consumer looking for upcoming events, B2C companies looking to participate, B2B companies looking to connect with other companies

Industry/Entity Type

It Company

Requirements
Must have
• The new design should help to achieve the following objectives:
1) Visitors should be able to easily identify and access the 2 different types of events (i.e. Trade Events and Consumer Events).
2) Visitors should be able to easily find events that interest them (e.g. filter by date, trade or consumer, category [i.e. beauty, retail, F&B, construction, etc.]).
3) Visitors should be able to access an event’s details page within 2 clicks from any page.

Main navigation to include the following links:
- About Us
- Calendar
- Consumer Events
- Trade Events
- Contact Us

Design for Three (3) pages required:
A. Homepage
- Clear differentiation and easy access to the 2 different types of events (trade and consumer)
- Featured area to showcase latest 4-5 events
- Quick way to access events calendar
- Clear call-to-action for newsletter signup
- Social media sharing widgets/buttons
- A section for latest news and press releases
- A section for featured testimonials

B. Events Listing Page
- List of links to all events
- Logos and/or photos of events
- Filter / tags to find events in a specific category (e.g. food, electronics, building & construction, etc.)

C. Events Details Page
- Photo strip to showcase event photos / brochure
- A section with event details (Date, Venue, Event Description, etc.)
- Call-to-action button to visit event website
- Call-to-action button to contact event sales team
- E.g. http://vantly-demo.com/user/brightfoxhk/brightfox-monday-2011 but with the photo strip permanently extended and of a shorter height. Event details and call-to-action buttons should also be easily seen

```html
<!DOCTYPE html>
<html lang="en">
<head>
<meta charset="utf-8">
<title>Tallwood Expos</title>
<link href="https://fonts.googleapis.com/css2?family=Arimo:wght@400;700&family=Noto+Sans:wght@400&display=swap" rel="stylesheet">
<style>
:root{
  --orange:#f7931e;
  --red:#d9481c;
  --red-dark:#c13c14;
  --brown:#4a2a14;
  --brown-dark:#3a2010;
  --footer-text:#e0702a;
  --footer-head:#f7a21b;
  --ink:#222;
  --white:#fff;
}
*{box-sizing:border-box;margin:0;padding:0}
html,body{width:867px;height:1200px;overflow:hidden}
body{position:relative;font-family:"Arimo",Arial,sans-serif;color:var(--ink);background:#f4f4f4}
h2,h3{font-weight:400}

/* header */
.site-header{position:absolute;left:0;top:0;width:867px;height:155px;
  background:linear-gradient(#fcb23a 0,#f99a25 40%,#f47f16 100%)}
.logo{position:absolute;z-index:3;left:62px;top:10px;width:146px;height:146px;border-radius:50%;
  background:var(--white);border:6px solid #ffd21f;box-shadow:0 2px 4px rgba(0,0,0,.25);
  display:flex;flex-direction:column;align-items:center;justify-content:center;text-align:center}
.logo-name{font-size:21px;font-weight:700;color:var(--red);line-height:1.05;margin-top:6px}
.logo-sub{font-size:8.5px;font-weight:700;color:#1f4e9c;margin-top:14px;white-space:nowrap}
.search{position:absolute;left:645px;top:56px;width:161px;height:22px;border-radius:4px;
  background:linear-gradient(#fff,#e9e9e9);border:1px solid #c7c7c7;box-shadow:inset 0 1px 2px rgba(0,0,0,.2)}
.search svg{position:absolute;right:4px;top:2px}
.main-nav{position:absolute;left:180px;top:108px;width:633px;height:40px;border-radius:3px;
  background:linear-gradient(#fff,#ececec);box-shadow:0 1px 3px rgba(0,0,0,.25)}
.nav-item{position:absolute;top:15px;font-size:11px;color:#111;letter-spacing:.1px;white-space:nowrap}
.nav-item.active{color:#ffc21a;font-weight:700;font-size:10.5px}
.dropdown{position:absolute;z-index:2;left:408px;top:113px;width:121px;height:71px;background:#2d2b2a;border-radius:3px}
.dropdown .nav-item{left:9px;top:10px}
.dropdown ul{list-style:none;position:absolute;left:9px;top:29px}
.dropdown li{font-size:8.5px;color:#eee;height:14px;white-space:nowrap}
.dropdown li::before{content:"›";color:var(--orange);margin-right:6px;font-weight:700}

/* hero */
.hero{position:absolute;left:0;top:155px;width:867px;height:316px;
  background:linear-gradient(#fbb23c,#f7951f 50%,#f38a1b)}
.slide{position:absolute;top:24px;width:224px;height:269px;border-radius:3px;overflow:hidden}
.slide-caption{position:absolute;left:0;bottom:0;width:100%;height:40px;background:rgba(0,0,0,.45);
  font-family:"Noto Sans",sans-serif;color:#fff;font-size:13.5px;padding:10px 0 0 6px;white-space:nowrap}
.arrow{position:absolute;top:125px;width:32px;height:32px;border-radius:50%;
  background:linear-gradient(#fff,#ddd);box-shadow:0 1px 3px rgba(0,0,0,.3)}
.arrow svg{position:absolute;left:9px;top:8px}

/* content */
.content{position:absolute;left:0;top:471px;width:867px;height:454px;
  background:linear-gradient(#dcdcdc 0,#f6f6f6 40px,#f6f6f6)}
.panel{position:absolute;left:58px;width:221px;border-radius:6px;background:linear-gradient(#f6f6f6,#dedede);
  border:1px solid #e2e2e2;box-shadow:0 0 3px rgba(0,0,0,.1)}
.tab{position:absolute;left:97px;top:500px;width:126px;height:35px;background:linear-gradient(#f06a2c,var(--red));
  color:#fff;font-size:10.5px;font-weight:700;text-align:center;padding-top:10px;border-radius:3px 3px 0 0;
  box-shadow:0 2px 3px rgba(0,0,0,.25);white-space:nowrap}
.field-label{position:absolute;font-size:8.5px;color:#333}
.field{position:absolute;left:119px;width:140px;height:23px;background:#fff;border:1px solid #c6c6c6;
  border-radius:4px;box-shadow:inset 0 1px 2px rgba(0,0,0,.15)}
.btn{position:absolute;left:148px;top:627px;width:59px;height:22px;border-radius:3px;
  background:linear-gradient(#ef6a30,var(--red-dark));color:#fff;font-size:10.5px;text-align:center;padding-top:5px}
.cal-head{position:absolute;left:64px;top:696px;width:208px;height:30px;border-radius:5px 5px 0 0;
  background:linear-gradient(#f06e34,var(--red));color:#fff;font-size:11.5px;font-weight:700;padding:8px 0 0 20px;word-spacing:6px}
.calendar{position:absolute;left:64px;top:730px;width:207px;border-collapse:collapse;background:#fff}
.calendar th,.calendar td{border:1px solid #c8c8c8;text-align:center;width:29.5px;color:#222}
.calendar th{font-size:8.5px;font-weight:400;height:22px}
.calendar td{font-size:11px;height:23.5px}
.calendar td.today{background:var(--red);color:#fff}
.section-title{position:absolute;font-size:12.5px;color:var(--red);letter-spacing:.1px;white-space:nowrap}
.welcome-text{position:absolute;left:511px;top:558px;width:285px;font-size:10px;line-height:22px;color:#444}
.rule{position:absolute;left:319px;top:665px;width:494px;border-top:1px dotted #888}
.event-logo{position:absolute;width:106px;height:58px;border:1px solid #ddd;border-radius:3px;background:#fff;padding:4px}
.event-logo div{width:100%;height:100%}
.event-info{position:absolute;width:126px;font-size:8.5px;color:#333;line-height:10px}
.event-info p+p{margin-top:10px}
.more{position:absolute;font-size:8.5px;color:var(--red)}

/* footer */
.footer{position:absolute;left:0;top:925px;width:867px;height:218px;background:linear-gradient(var(--brown),var(--brown-dark))}
.foot-title{position:absolute;top:17px;font-size:13px;color:var(--footer-head);padding-bottom:4px;border-bottom:1px dotted #a06a3a;white-space:nowrap}
.foot-text{position:absolute;font-size:8.5px;line-height:13.5px;color:var(--footer-text)}
.foot-date{position:absolute;font-size:8.5px;color:#f3e2cc}
.foot-more{position:absolute;font-size:8.5px;color:#f7a21b}
.bullet{position:absolute;width:9px;height:9px;border-radius:50%;background:#fff}
.avatar{position:absolute;width:45px;height:46px;border:2px solid #fff;background:linear-gradient(#d7c3b0,#9a7f6a)}
.bottom-bar{position:absolute;left:0;top:1143px;width:867px;height:57px;background:linear-gradient(#fbaa34,#f58a1c)}
.social{position:absolute;top:14px;width:25px;height:25px;border-radius:50%;background:#fff;box-shadow:0 1px 2px rgba(0,0,0,.3)}
.legal{position:absolute;left:299px;top:14px;font-size:8.5px;color:#222;word-spacing:1px;white-space:nowrap}
.copy{position:absolute;left:369px;top:36px;font-size:9px;color:#222;white-space:nowrap}
</style>
</head>
<body>

<header class="site-header">
  <nav class="main-nav">
    <span class="nav-item" style="left:57px">ABOUT US</span>
    <span class="nav-item" style="left:145px">CALENDAR</span>
    <span class="nav-item" style="left:378px">TRADE EVENTS</span>
    <span class="nav-item" style="left:492px">CONTACT US</span>
  </nav>
  <div class="logo"><span class="logo-name">Tallwood<br>Expos</span><span class="logo-sub">A SUBSIDIARY OF NVM</span></div>
  <div class="search">
    <svg width="18" height="18" viewBox="0 0 18 18"><circle cx="7" cy="7" r="5" fill="none" stroke="#777" stroke-width="2"/><line x1="11" y1="11" x2="16" y2="16" stroke="#777" stroke-width="3"/></svg>
  </div>
</header>
<div class="dropdown">
  <span class="nav-item active">CONSUMER EVENTS</span>
  <ul><li>EVENT 1</li><li>EVENT 2</li><li>EVENT 3</li></ul>
</div>

<section class="hero">
  <div class="slide" style="left:78px;background:linear-gradient(#6a4a3a,#2a2230)" role="img" aria-label="Photo of an exhibition booth with visitors">
    <div class="slide-caption">Lorem ipsum dolor sit amet elit.</div>
  </div>
  <div class="slide" style="left:319px;background:linear-gradient(#4a4a5e,#2a2838)" role="img" aria-label="Photo of a stage show with confetti at a consumer event">
    <div class="slide-caption">Lorem ipsum dolor sit amet elit.</div>
  </div>
  <div class="slide" style="left:560px;background:linear-gradient(#c9b8a6,#5a4a48)" role="img" aria-label="Photo of visitors at an event booth">
    <div class="slide-caption">Lorem ipsum dolor sit amet elit.</div>
  </div>
  <div class="arrow" style="left:56px"><svg width="12" height="16"><path d="M10 1 L2 8 L10 15" fill="none" stroke="#999" stroke-width="2"/></svg></div>
  <div class="arrow" style="left:771px"><svg width="12" height="16"><path d="M3 1 L11 8 L3 15" fill="none" stroke="#999" stroke-width="2"/></svg></div>
</section>

<main class="content"></main>

<div class="panel" style="top:518px;height:155px"></div>
<div class="tab">NEWSLETTER SIGNUP</div>
<span class="field-label" style="left:74px;top:560px">NAME :</span>
<div class="field" style="top:556px"></div>
<span class="field-label" style="left:74px;top:596px">EMAIL :</span>
<div class="field" style="top:591px"></div>
<div class="btn">Submit</div>

<div class="panel" style="top:690px;height:186px"></div>
<div class="cal-head">JANUARY 2012</div>
<table class="calendar">
  <tr><th>SUN</th><th>MON</th><th>TUE</th><th>WED</th><th>THU</th><th>FRI</th><th>SAT</th></tr>
  <tr><td>1</td><td>2</td><td>3</td><td>4</td><td>5</td><td>6</td><td>7</td></tr>
  <tr><td>8</td><td>9</td><td>10</td><td>11</td><td>12</td><td>13</td><td>14</td></tr>
  <tr><td>15</td><td>16</td><td>17</td><td>18</td><td>19</td><td>20</td><td>21</td></tr>
  <tr><td>22</td><td>23</td><td>24</td><td>25</td><td>26</td><td class="today">27</td><td>28</td></tr>
  <tr><td>29</td><td>30</td><td>31</td><td></td><td></td><td></td><td></td></tr>
</table>

<h2 class="section-title" style="left:312px;top:513px">WELCOME TO TALLWOOD EXPOS</h2>
<div class="event-logo" style="left:314px;top:544px;width:186px;height:106px;padding:3px" role="img" aria-label="Photo of a group of young visitors at an expo"><div style="background:linear-gradient(#5a5a6a,#3a4a5a)"></div></div>
<p class="welcome-text">Bringing about a Whole new dimension of audience experience and engagement by organizing events with focus on differentiated themes and event concepts</p>
<div class="rule"></div>
<h2 class="section-title" style="left:320px;top:682px">FEATURED AREA</h2>

<div class="event-logo" style="left:317px;top:715px" role="img" aria-label="Little Ones Fair event logo"><div style="background:linear-gradient(90deg,#f4c13a,#e94a8a,#3a9ad9)"></div></div>
<div class="event-info" style="left:429px;top:715px"><p>Date: 15 - 17 May 2012,<br>10am - 6pm</p><p>Harbour Point Hall, Lumen City</p><p>Admission is restricted to trade professionals</p></div>
<span class="more" style="left:324px;top:782px">read more...</span>

<div class="event-logo" style="left:579px;top:713px" role="img" aria-label="Print and Paper Fair event logo"><div style="background:linear-gradient(90deg,#e94a8a,#f7b52a,#3ab0d9)"></div></div>
<div class="event-info" style="left:697px;top:712px"><p>Date: 15 - 17 May 2012,<br>10am - 6pm</p><p>Harbour Point Hall, Lumen City</p><p>Admission is restricted to trade professionals</p></div>
<span class="more" style="left:582px;top:780px">read more...</span>

<div class="event-logo" style="left:318px;top:837px" role="img" aria-label="Play Licence Show event logo"><div style="background:linear-gradient(90deg,#c8221e,#2a2a2a)"></div></div>
<div class="event-info" style="left:433px;top:834px"><p>Date: 15 - 17 May 2012,<br>10am - 6pm</p><p>Harbour Point Hall, Lumen City</p><p>Admission is restricted to trade professionals</p></div>
<span class="more" style="left:322px;top:904px">read more...</span>

<div class="event-logo" style="left:579px;top:837px" role="img" aria-label="Flavour Fair event logo"><div style="background:linear-gradient(90deg,#c8221e,#4a9a3a)"></div></div>
<div class="event-info" style="left:694px;top:834px"><p>Date: 15 - 17 May 2012,<br>10am - 6pm</p><p>Harbour Point Hall, Lumen City</p><p>Admission is restricted to trade professionals</p></div>
<span class="more" style="left:586px;top:902px">read more...</span>

<footer class="footer">
  <h3 class="foot-title" style="left:88px;width:160px">LATEST NEWS</h3>
  <span class="bullet" style="left:85px;top:48px"></span>
  <span class="foot-date" style="left:104px;top:46px">27 Jan 2012</span>
  <p class="foot-text" style="left:102px;top:60px;width:165px">Lorem ipsum dolor sit amet, consectetuer adipiscing elit. Nam nibh. Lorem ipsum dolor sit amet.</p>
  <span class="foot-more" style="left:102px;top:103px">Read More &gt;&gt;</span>
  <span class="bullet" style="left:85px;top:139px"></span>
  <span class="foot-date" style="left:102px;top:136px">27 Jan 2012</span>
  <p class="foot-text" style="left:102px;top:151px;width:165px">Lorem ipsum dolor sit amet, consectetuer adipiscing elit. Nam nibh. Lorem ipsum dolor sit amet.</p>
  <span class="foot-more" style="left:102px;top:197px">Read More &gt;&gt;</span>

  <h3 class="foot-title" style="left:334px;width:160px">PRESS RELEASES</h3>
  <p class="foot-text" style="left:334px;top:46px">Article Title&nbsp; :</p>
  <p class="foot-text" style="left:388px;top:46px;width:120px">NVM enters new field of Mice business</p>
  <p class="foot-text" style="left:334px;top:80px">Source&nbsp;&nbsp;&nbsp;&nbsp;&nbsp;&nbsp;&nbsp; :&nbsp; The Daily Ledger - Jun 05 2008</p>
  <p class="foot-text" style="left:334px;top:102px">Date&nbsp;&nbsp;&nbsp;&nbsp;&nbsp;&nbsp;&nbsp;&nbsp;&nbsp;&nbsp;&nbsp; :&nbsp; 05-01-2012</p>
  <p class="foot-text" style="left:334px;top:127px">Media Article&nbsp; :</p>
  <span class="foot-more" style="left:400px;top:126px;color:#f7c21b">DOWNLOAD</span>

  <h3 class="foot-title" style="left:581px;width:160px">FEATURED TESTIMONIALS</h3>
  <div class="avatar" style="left:587px;top:45px" role="img" aria-label="Portrait photo of a client"></div>
  <span class="foot-date" style="left:641px;top:42px">26 Jan 2012</span>
  <p class="foot-text" style="left:641px;top:56px;width:165px">Lorem ipsum dolor sit amet, consectetuer adipiscing elit. Nam nibh. Lorem ipsum dolor sit amet.</p>
  <span class="foot-more" style="left:752px;top:103px">Read More &gt;&gt;</span>
  <div class="avatar" style="left:587px;top:146px" role="img" aria-label="Portrait photo of a client"></div>
  <span class="foot-date" style="left:641px;top:136px">26 Jan 2012</span>
  <p class="foot-text" style="left:641px;top:150px;width:165px">Lorem ipsum dolor sit amet, consectetuer adipiscing elit. Nam nibh. Lorem ipsum dolor sit amet.</p>
  <span class="foot-more" style="left:749px;top:196px">Read More &gt;&gt;</span>
</footer>

<div class="bottom-bar">
  <span class="social" style="left:98px" aria-label="Social link 1"></span>
  <span class="social" style="left:129px" aria-label="Social link 2"></span>
  <span class="social" style="left:160px" aria-label="Social link 3"></span>
  <span class="social" style="left:191px" aria-label="Social link 4"></span>
  <p class="legal">PRIVACY POLICY &nbsp;&nbsp;| &nbsp;&nbsp;DISCLAIMER &nbsp;&nbsp;| &nbsp;&nbsp;TERMS &amp; CONDITIONS &nbsp;| &nbsp;&nbsp;CONTACT US</p>
  <p class="copy">Copyright © Tallwood Expos All Rights Reserved</p>
</div>

</body>
</html>
```